Kentucky residential recovery center needs a flyer design

We need a flyer design for a 16 bed male residential/inpatient recovery center based in Richmond, Kentucky. The facility provides short term (average 30 day) treatment to those struggling with substace abuse and addiction. The design should communicate trust, assurance, safety.
Our wesite provides more information https://corvalmend.org/treatment-services/residential-treatment/

Target Market(s)

Men (typically 30-50) struggling with substance addiction

```html
<!DOCTYPE html>
<html lang="en">
<head>
<meta charset="utf-8">
<title>Corval Mend – Residential Treatment Flyer</title>
<link href="https://fonts.googleapis.com/css2?family=Jost:wght@400;500;600;700;800&family=EB+Garamond:wght@400;500;700&family=Roboto+Slab:wght@600;700&display=swap" rel="stylesheet">
<style>
  :root{
    --navy:#0d0e7a;
    --green:#16b43c;
    --green-soft:#6cc97e;
    --green-text:#1f9a3a;
    --white:#ffffff;
    --ink:#4a4a4a;
    --page:#8f8f8f;
    --paper:#f3f5f6;
  }
  *{box-sizing:border-box;margin:0;padding:0}
  html,body{width:1200px;height:1200px;overflow:hidden;background:var(--page)}
  .canvas{position:relative;width:1200px;height:1200px;background:var(--page)}
  .flyer{position:absolute;left:152px;top:20px;width:896px;height:1160px;overflow:hidden;background:var(--paper);font-family:"Jost",sans-serif}
  .flyer-shapes{position:absolute;inset:0}
  .hero-photo{position:absolute;left:0;top:14px;width:340px;height:498px;border-radius:0 120px 30px 0}
  .brand{position:absolute;left:600px;top:128px;display:flex;align-items:center;gap:12px}
  .brand-dot{width:26px;height:26px;border-radius:50%;background:var(--green)}
  .brand-name{font-weight:700;font-size:34px;color:var(--navy);letter-spacing:1px}
  .headline{position:absolute;right:58px;top:262px;text-align:right;line-height:1}
  .headline-main{font-weight:800;font-size:54px;color:var(--white);-webkit-text-stroke:6px var(--green);paint-order:stroke fill;letter-spacing:-.5px}
  .headline-sub{font-weight:800;font-size:25px;color:var(--green);-webkit-text-stroke:5px var(--white);paint-order:stroke fill;margin-top:6px}
  .intro{position:absolute;right:58px;top:402px;width:470px;text-align:right;color:var(--white);font-size:18px;line-height:27px;font-weight:500;text-transform:uppercase}
  .intro-rule{position:absolute;right:58px;top:490px;width:300px;height:1px;background:rgba(255,255,255,.6)}
  .intro-stat{position:absolute;right:58px;top:510px;width:545px;text-align:right;color:var(--white);font-size:13.5px;line-height:26px;letter-spacing:-.2px}
  .tagline{position:absolute;left:215px;width:620px;top:570px;text-align:center;font-weight:600;font-size:35px;color:var(--white);-webkit-text-stroke:6px var(--navy);paint-order:stroke fill;white-space:nowrap}
  .issues-title{position:absolute;left:66px;top:658px;font-size:20px;color:var(--navy);font-weight:500}
  .issues{position:absolute;left:42px;top:700px;width:395px;height:180px;border-radius:10px;background:var(--green-soft);padding:16px 0 0 28px;list-style:none}
  .issues li{display:flex;align-items:center;gap:18px;height:40px;font-family:"Roboto Slab",serif;font-weight:700;font-size:21px;color:var(--navy)}
  .issue-icon{width:20px;height:20px;border-radius:50%;background:var(--navy);flex:none}
  .program{position:absolute;left:60px;top:889px;font-size:20px;color:var(--navy);font-weight:500}
  .contact{position:absolute;left:75px;top:925px;list-style:none;color:var(--ink);font-size:20px}
  .contact li{display:flex;align-items:flex-start;gap:12px;margin-bottom:10px;line-height:26px}
  .contact svg{flex:none;margin-top:3px}
  .visit{position:absolute;left:56px;top:1072px;font-size:14px;color:var(--navy)}
  .url{position:absolute;left:42px;top:1097px;width:515px;height:31px;border-radius:16px;background:var(--navy);color:var(--white);text-align:center;font-weight:700;font-size:19px;letter-spacing:7px;line-height:31px;box-shadow:0 3px 4px rgba(0,0,0,.3)}
  .why{position:absolute;left:467px;top:664px;width:385px;font-family:"EB Garamond",serif}
  .why-title{font-weight:500;font-size:22px;color:var(--navy);margin-bottom:8px;white-space:nowrap}
  .why-title strong{font-weight:700;letter-spacing:.5px}
  .why h3{font-weight:500;font-size:15.5px;color:var(--green-text);margin:6px 0 8px;letter-spacing:.3px}
  .why p{font-size:13px;line-height:13.6px;color:var(--ink);margin-bottom:10px}
</style>
</head>
<body>
<div class="canvas">
  <article class="flyer">
    <svg class="flyer-shapes" viewBox="0 0 896 1160" width="896" height="1160" aria-hidden="true">
      <defs>
        <linearGradient id="lowerWash" x1="0" y1="0" x2="1" y2="1">
          <stop offset="0" stop-color="#eef0f1"/>
          <stop offset="1" stop-color="#f9fafa"/>
        </linearGradient>
      </defs>
      <rect x="0" y="0" width="896" height="1160" fill="url(#lowerWash)"/>
      <path d="M0 0 H896 V555 C700 565 420 590 180 640 L0 660 Z" fill="var(--navy)"/>
      <path d="M241 0 H896 V405 C700 400 540 330 430 230 C360 160 290 80 241 0 Z" fill="var(--green)"/>
      <path d="M337 0 H896 V388 C720 380 580 330 480 240 C420 170 370 90 337 0 Z" fill="var(--white)"/>
      <path d="M200 615 C420 575 680 560 896 545 V600 C700 590 470 615 300 640 Z" fill="var(--green)"/>
      <path d="M896 1035 V1160 H544 C660 1110 780 1070 896 1035 Z" fill="var(--green)"/>
      <path d="M896 1035 C800 1060 720 1090 640 1130 C740 1075 820 1045 896 1022 Z" fill="var(--navy)"/>
    </svg>

    <div class="hero-photo" role="img" aria-label="Photo of a smiling bearded man in a grey t-shirt holding a certificate of completion" style="background:linear-gradient(160deg,#3a3f8c 0%,#6d7280 35%,#8a8c92 60%,#b7b9bd 100%)"></div>

    <div class="brand">
      <span class="brand-dot"></span>
      <span class="brand-name">Corval Mend</span>
    </div>

    <h1 class="headline">
      <div class="headline-main">KENTUCKYS</div>
      <div class="headline-sub">LEADING DRUG &amp; ALCOHOL</div>
      <div class="headline-sub">ADDICTION TREATMENT</div>
    </h1>

    <p class="intro">Providing the highest level of rehab services for patients diagnosed with alchohol or other drug or substance addiction.</p>
    <div class="intro-rule"></div>
    <p class="intro-stat">94% of those suffering from substance use disorder stay in active addiction without an intervention. We offer the most effective and comfortable treatment that leads to success.</p>

    <h2 class="tagline">ADDICTION TREATMENT THAT WORKS</h2>

    <h2 class="issues-title">WHAT ISSUES CAN BE TREATED?</h2>
    <ul class="issues">
      <li><span class="issue-icon"></span>ALCOHOLISM</li>
      <li><span class="issue-icon"></span>DRUG ADDICTION</li>
      <li><span class="issue-icon"></span>MEDICATION ADDICTION</li>
      <li><span class="issue-icon"></span>BEHAVIORAL HEALTH</li>
    </ul>

    <h2 class="program">RESIDENTIAL/INPATIENT TREATMENT</h2>
    <ul class="contact">
      <li>
        <svg width="22" height="22" viewBox="0 0 24 24"><circle cx="12" cy="12" r="12" fill="#0d0e7a"/><path d="M8 6.5c.6-.4 1.3-.3 1.6.3l1 1.8c.3.5.2 1.1-.3 1.5l-.7.5c.6 1.4 1.6 2.5 3 3.1l.5-.7c.4-.5 1-.6 1.5-.3l1.8 1c.6.3.7 1 .3 1.6-.9 1.2-2.4 1.6-3.8 1-3-1.3-5.3-3.6-6.5-6.5-.5-1.4-.1-2.9 1.1-3.8z" fill="#fff"/></svg>
        859-555-0147
      </li>
      <li>
        <svg width="22" height="22" viewBox="0 0 24 24"><circle cx="12" cy="12" r="12" fill="#0d0e7a"/><rect x="6" y="8" width="12" height="8" rx="1" fill="none" stroke="#fff" stroke-width="1.5"/><path d="M6 8l6 5 6-5" fill="none" stroke="#fff" stroke-width="1.5"/></svg>
        ADMISSIONS@CORVALMEND.COM
      </li>
      <li>
        <svg width="22" height="28" viewBox="0 0 22 28"><path d="M11 1C5.5 1 2 5 2 9.8 2 16 11 27 11 27s9-11 9-17.2C20 5 16.5 1 11 1z" fill="#0d0e7a"/><circle cx="11" cy="10" r="3.5" fill="#fff"/></svg>
        <span>2418 Harmon Ridge Rd, Richmond<br>&nbsp;KY 40475, United States</span>
      </li>
    </ul>

    <p class="visit">Visit us online for more information</p>
    <div class="url">www.corvalmend.org</div>

    <section class="why">
      <h2 class="why-title">WHY <strong>TREATMENT HERE</strong> WORKS</h2>
      <h3>1. EVIDENCE BASED TREATMENT</h3>
      <p>We use evidence-based treatment that has been scientifically tested and proven to produce positive results. Ranging from cognitive behaviour therapy to dialectical therapy, we do what it takes to make you healthy.</p>
      <h3>2. INDIVIDUALIZED</h3>
      <p>You deserve individualized attention from experienced professionals who actually care. Our reputation, small case load and success rates mean you are given the best treatment from leading experts.</p>
      <h3>3. TELEMEDICINE</h3>
      <p>Corval Mend is offering aspects of its treatment program via tele-health services to meet the need of clients seeking treatment from the convenience of their homes.</p>
      <h3>4. MEDICATION ASSISTED TREATMENT</h3>
      <p>Medication assisted treatment helps to relieve withdrawal symptoms and cravings which makes going clean easier. We treat addiction with FDA-approved medicines to help you focus on your recovery. We prescribe medicines such as Bunalex (a treatment combining buprenorphine and naloxone), Naltrevia (a naltrexone treatment), and Bupredex (a buprenorphine treatment)</p>
    </section>
  </article>
</div>
</body>
</html>
```